Law Firm Business Card

This is a business card for a law firm that serves US military and veterans.

The card must have ONLY the following (we want an uncluttered look):

- Company logo (PNG, GIF, JPEG copies uploaded)
- A tagline reading: "a law firm for service members and veterans"
- My name and title: "Tobias Marlow" and "Attorney"
- My email: "tobias.marlow@brinmoorlegal.com"
- My number: "855-FIRM-ONE (347-6663)"

We are looking for a clean, simple layout with only the above information, likely printed on a bright white cotton stock. The font of our logo is DIN 1451, and the font used on our website is Helvetica Neue. The color of our logo is #336699, and we probably want the tagline in that color also, and my contact information in a dark grey. Please review our website at www.brinmoorlegal.com to ensure your card design complements our website style.

Thanks and we look forward to seeing your submissions.

A few notes:

- Two-sided submissions are ok
- Please don't add graphics (scales of justice, judges hammer, etc)

```html
<!DOCTYPE html>
<html lang="en">
<head>
<meta charset="utf-8">
<title>Brinmoor Legal — Business Card</title>
<link href="https://fonts.googleapis.com/css2?family=Barlow+Condensed:wght@600&family=Inter:wght@400;500&display=swap" rel="stylesheet">
<style>
  :root {
    --brand-blue: #336699;
    --ink-grey: #3a3d42;
    --muted-grey: #6b6f75;
    --card-white: #ffffff;
    --backdrop: #dcdad6;
    --logo-font: "Barlow Condensed", "DIN 1451", sans-serif;
    --body-font: "Inter", "Helvetica Neue", Helvetica, Arial, sans-serif;
  }
  * { box-sizing: border-box; margin: 0; padding: 0; }
  html, body {
    width: 1200px;
    height: 848px;
    overflow: hidden;
    background: var(--backdrop);
  }
  .sheet {
    width: 1200px;
    height: 848px;
    display: flex;
    flex-direction: column;
    align-items: center;
    justify-content: center;
    gap: 32px;
  }
  .card {
    position: relative;
    width: 660px;
    height: 377px;
    background: var(--card-white);
    box-shadow: 0 6px 18px rgba(0, 0, 0, 0.18);
    overflow: hidden;
  }

  /* Front */
  .front .wordmark {
    position: absolute;
    top: 108px;
    left: 0;
    right: 0;
    text-align: center;
    font-family: var(--logo-font);
    font-weight: 600;
    font-size: 68px;
    letter-spacing: 1px;
    text-transform: uppercase;
    color: var(--brand-blue);
  }
  .front .tagline {
    position: absolute;
    bottom: 42px;
    left: 0;
    right: 0;
    text-align: center;
    font-family: var(--body-font);
    font-size: 17px;
    color: var(--brand-blue);
  }
  .front .base-band {
    position: absolute;
    left: 0;
    right: 0;
    bottom: 0;
    height: 24px;
    background: var(--brand-blue);
  }

  /* Back */
  .back .wordmark {
    position: absolute;
    top: 62px;
    left: 44px;
    font-family: var(--logo-font);
    font-weight: 600;
    font-size: 42px;
    letter-spacing: 0.5px;
    text-transform: uppercase;
    color: var(--brand-blue);
  }
  .back .tagline-box {
    position: absolute;
    top: 58px;
    right: 0;
    width: 226px;
    height: 74px;
    padding: 12px 18px;
    background: var(--brand-blue);
    color: var(--card-white);
    font-family: var(--body-font);
    font-size: 14px;
    line-height: 1.3;
  }
  .back .person {
    position: absolute;
    left: 44px;
    bottom: 52px;
    font-family: var(--body-font);
  }
  .back .person-name {
    font-size: 17px;
    font-weight: 500;
    color: var(--brand-blue);
  }
  .back .person-title {
    margin-top: 3px;
    font-size: 14px;
    color: var(--muted-grey);
  }
  .back .contact {
    position: absolute;
    right: 36px;
    bottom: 54px;
    text-align: right;
    font-family: var(--body-font);
    font-size: 13px;
    line-height: 1.6;
    color: var(--ink-grey);
  }
</style>
</head>
<body>
  <main class="sheet">
    <section class="card front" aria-label="Card front">
      <div class="wordmark">Brinmoor Legal</div>
      <p class="tagline">a law firm for service members and veterans</p>
      <div class="base-band"></div>
    </section>

    <section class="card back" aria-label="Card back">
      <div class="wordmark">Brinmoor Legal</div>
      <p class="tagline-box">a law firm for<br>service members<br>and veterans</p>
      <div class="person">
        <p class="person-name">Tobias Marlow</p>
        <p class="person-title">Attorney</p>
      </div>
      <div class="contact">
        <p class="contact-email">tobias.marlow@brinmoorlegal.com</p>
        <p class="contact-phone">855-FIRM-ONE (347-6663)</p>
      </div>
    </section>
  </main>
</body>
</html>
```